Commercial Real Estate Property Sign

Design a 4' x 4' sign that pops. Refer to examples.

Must include the following information:
A space to list (For Sale, For Lease, Build-to-Suite or Available)
BrightKeel,LLC
Commercial Real Estate
company website
My Name (Marcus Pellow)
My Phone #

Industry/Entity Type

Real Estate

```html
<!DOCTYPE html>
<html lang="en">
<head>
<meta charset="UTF-8">
<title>BrightKeel LLC – Commercial Real Estate Sign</title>
<link href="https://fonts.googleapis.com/css2?family=Barlow:wght@400;500;700&display=swap" rel="stylesheet">
<style>
  :root {
    --charcoal: #3a3a3a;
    --orange: #e96508;
    --ink: #1f1f1f;
    --white: #ffffff;
  }
  * { margin: 0; padding: 0; box-sizing: border-box; }
  html, body {
    width: 1200px;
    height: 1200px;
    overflow: hidden;
    background: var(--charcoal);
  }
  .sign {
    position: relative;
    width: 1200px;
    height: 1200px;
    font-family: "Barlow", sans-serif;
  }
  .band { position: absolute; left: 0; width: 1200px; }

  /* Header band */
  .header { top: 0; height: 240px; background: var(--charcoal); }
  .brand {
    position: absolute;
    top: 50px;
    left: 0;
    width: 1200px;
    text-align: center;
  }
  .brand-name {
    display: inline-block;
    color: var(--white);
    font-weight: 400;
    font-size: 102px;
    line-height: 1;
    letter-spacing: 22px;
    margin-right: -22px;
  }
  .tagline-row {
    position: absolute;
    top: 162px;
    left: 0;
    width: 1200px;
    display: flex;
    align-items: center;
  }
  .tagline-rule {
    flex: 1;
    height: 3px;
    background: var(--orange);
  }
  .tagline {
    color: var(--white);
    font-weight: 400;
    font-size: 50px;
    line-height: 1;
    padding: 0 12px;
    letter-spacing: 0.5px;
  }

  /* Contact band */
  .contact {
    top: 240px;
    height: 552px;
    background: var(--orange);
    display: flex;
    flex-direction: column;
    align-items: center;
    justify-content: center;
    color: var(--ink);
  }
  .agent-name {
    font-weight: 400;
    font-size: 136px;
    line-height: 1.02;
    letter-spacing: 3px;
  }
  .agent-phone {
    font-weight: 700;
    font-size: 126px;
    line-height: 1.1;
    letter-spacing: 4px;
  }

  /* Listing status band */
  .status {
    top: 792px;
    height: 240px;
    background: var(--charcoal);
    display: flex;
    flex-direction: column;
    align-items: center;
    justify-content: center;
    gap: 4px;
    color: var(--white);
    font-weight: 700;
    font-size: 86px;
    line-height: 1.2;
    letter-spacing: 1px;
  }
  .status-line { display: flex; align-items: center; gap: 28px; }
  .status-divider {
    width: 3px;
    height: 70px;
    background: var(--white);
  }
  .initial { color: var(--orange); }

  /* Website band */
  .web {
    top: 1032px;
    height: 168px;
    background: var(--orange);
    display: flex;
    align-items: center;
    justify-content: center;
    gap: 26px;
    color: var(--ink);
  }
  .web-icon { width: 46px; height: 46px; }
  .web-address {
    font-weight: 700;
    font-size: 86px;
    line-height: 1;
    letter-spacing: 1px;
  }
</style>
</head>
<body>
  <main class="sign">
    <header class="band header">
      <div class="brand">
        <span class="brand-name">BrightKeel LLC</span>
      </div>
      <div class="tagline-row">
        <span class="tagline-rule"></span>
        <span class="tagline">Commercial Real Estate</span>
        <span class="tagline-rule"></span>
      </div>
    </header>

    <section class="band contact">
      <p class="agent-name">Marcus Pellow</p>
      <p class="agent-phone">469.555.0172</p>
    </section>

    <section class="band status">
      <p class="status-line">
        <span><span class="initial">F</span>or Sale</span>
        <span class="status-divider"></span>
        <span><span class="initial">F</span>or Lease</span>
      </p>
      <p class="status-line">
        <span><span class="initial">B</span>uild-to-Suite or Available</span>
      </p>
    </section>

    <footer class="band web">
      <svg class="web-icon" viewBox="0 0 40 40" aria-hidden="true">
        <g fill="none" stroke="#1f1f1f" stroke-width="2.5">
          <circle cx="20" cy="20" r="17"/>
          <ellipse cx="20" cy="20" rx="7.5" ry="17"/>
          <line x1="3" y1="20" x2="37" y2="20"/>
          <path d="M6 11 H34 M6 29 H34"/>
        </g>
      </svg>
      <span class="web-address">www.mybrightkeel.com</span>
    </footer>
  </main>
</body>
</html>
```